Business card for Eyelash extension salon in Beverly Hills,California USA

We need new business card for our salon in Beverly Hills. The salon name is 'Lashvera' . We would like to have...Business name: Lashvera Name of person: will provide later Address 4720 N.Alder Crest Ave Beverly Hills , CA 90210 Phone: will provide later (Text only) Web: www.lashverastudio.example Snapgrid icon, Circlebook icon follow us for seasonal campaign and news @lashverastudiolounge Design should look elegant, high-end, clean, simple, cohesive with my brand. Please refer my brand board. Business name color will be metallic bronzy color. Im thinking grey background or white background. Thanks

Target Market(s)

25-35. Gender neutral. People who are in Entertainment business industry.
This is High-end Eyelash extension salon in Beverly Hills

Industry/Entity Type

Beauty Salon

Contact Information for Business Card

Business name: Lashvera
Name of person: will provide later
Address 4720 N.Alder Crest Ave Beverly Hills , CA 90210
Phone: will provide later (Text only)
Web: www.lashverastudio.example
Snapgrid icon, Circlebook icon
follow us for seasonal campaign and news @lashverastudiolounge

Requirements
Must have
• Beautiful, elegant, clean and simple look but very attractive and modern
Should not have
• We don't like too clutter, too busy designs.

```html
<!DOCTYPE html>
<html lang="en">
<head>
<meta charset="utf-8">
<title>Lashvera Business Card</title>
<link href="https://fonts.googleapis.com/css2?family=Montserrat:wght@300;400;700&display=swap" rel="stylesheet">
<style>
  :root {
    --page: #ece8e4;
    --card-white: #ffffff;
    --bronze: #8a6a55;
    --bronze-back: #8e6d5a;
    --ink: #4a4a4a;
    --muted: #6b6b6b;
    --silhouette: #ece8e6;
    --on-dark: #ffffff;
  }
  * { box-sizing: border-box; margin: 0; padding: 0; }
  html, body { width: 1200px; height: 960px; overflow: hidden; }
  body {
    background: var(--page);
    font-family: "Montserrat", Arial, sans-serif;
    position: relative;
  }
  .card {
    position: absolute;
    left: 232px;
    width: 736px;
    height: 420px;
    border-radius: 4px;
    box-shadow: 0 10px 28px rgba(0,0,0,.14);
    overflow: hidden;
  }
  /* Back side */
  .card-back { top: 40px; background: var(--bronze-back); color: var(--on-dark); text-align: center; }
  .card-back .brand-name {
    margin-top: 110px;
    font-size: 74px; font-weight: 300; letter-spacing: 4px;
  }
  .card-back .brand-place {
    margin-top: 6px; font-size: 13px; letter-spacing: 5px; text-transform: uppercase;
  }
  .social-row { display: flex; justify-content: center; gap: 28px; margin-top: 36px; font-size: 13px; }
  .social-item { display: flex; align-items: center; gap: 8px; }
  .social-dot { width: 22px; height: 22px; border: 1.5px solid var(--on-dark); border-radius: 50%; }
  .follow-line { margin-top: 16px; font-size: 17px; letter-spacing: .5px; }
  .handle { margin-top: 4px; font-size: 17px; }

  /* Front side */
  .card-front { top: 500px; background: var(--card-white); }
  .figure-area {
    position: absolute; right: 70px; bottom: 0; width: 250px; height: 170px;
    background: linear-gradient(180deg, rgba(236,232,230,0) 0%, var(--silhouette) 45%);
    z-index: 0;
  }
  .person-name {
    position: absolute; left: 56px; top: 56px;
    font-size: 30px; font-weight: 700; letter-spacing: 2px; color: var(--bronze);
  }
  .person-role { position: absolute; left: 56px; top: 96px; font-size: 17px; color: var(--muted); letter-spacing: .5px; }
  .divider { position: absolute; left: 56px; top: 164px; width: 62px; height: 1px; background: var(--bronze); }
  .address { position: absolute; left: 56px; top: 238px; font-size: 20px; line-height: 30px; color: var(--ink); z-index: 1; }
  .contact { position: absolute; left: 56px; top: 316px; font-size: 20px; color: var(--ink); z-index: 1; white-space: nowrap; }
  .contact-row { display: flex; align-items: center; gap: 14px; height: 34px; }
  .contact-row svg { width: 18px; height: 18px; flex: none; }
  .logo-block { position: absolute; right: 60px; top: 100px; text-align: center; color: var(--bronze); z-index: 1; }
  .logo-block .brand-name { font-size: 62px; font-weight: 300; letter-spacing: 3px; }
  .logo-block .brand-place { margin-top: 8px; font-size: 12px; letter-spacing: 5px; text-transform: uppercase; }
</style>
</head>
<body>
  <section class="card card-back">
    <div class="brand-name">Lashvera</div>
    <div class="brand-place">Beverly Hills</div>
    <div class="social-row">
      <span class="social-item"><span class="social-dot"></span>Circlebook</span>
      <span class="social-item"><span class="social-dot"></span>Snapgrid</span>
    </div>
    <p class="follow-line">Follow Us For Seasonal Campaign News</p>
    <p class="handle">@lashverastudiolounge</p>
  </section>

  <section class="card card-front">
    <div class="figure-area" role="img" aria-label="Faint silhouettes of two fashion models"></div>
    <h1 class="person-name">Maren Castell</h1>
    <p class="person-role">Fashion Marketing</p>
    <div class="divider"></div>
    <p class="address">4720 N.Alder Crest Ave<br>Beverly Hills , CA 90210</p>
    <div class="contact">
      <div class="contact-row">
        <svg viewBox="0 0 24 24" aria-hidden="true"><path fill="#5a5a5a" d="M6.6 10.8a15.1 15.1 0 0 0 6.6 6.6l2.2-2.2a1 1 0 0 1 1-.25 11.4 11.4 0 0 0 3.6.57 1 1 0 0 1 1 1V20a1 1 0 0 1-1 1A17 17 0 0 1 3 4a1 1 0 0 1 1-1h3.5a1 1 0 0 1 1 1c0 1.25.2 2.45.57 3.57a1 1 0 0 1-.25 1z"/></svg>
        <span>1 555 010 2048</span>
      </div>
      <div class="contact-row">
        <svg viewBox="0 0 24 24" aria-hidden="true" fill="none" stroke="#8a6a55" stroke-width="1.6"><circle cx="12" cy="12" r="9"/><ellipse cx="12" cy="12" rx="4" ry="9"/><path d="M3 12h18M5 7h14M5 17h14"/></svg>
        <span>www.lashverastudio.example</span>
      </div>
    </div>
    <div class="logo-block">
      <div class="brand-name">Lashvera</div>
      <div class="brand-place">Beverly Hills</div>
    </div>
  </section>
</body>
</html>
```